Luxury Wine Label for New Startup Winery

We need a wine label for our new winery startup. We have worked with a local designer but do not feel the resulting label / logo have the elevation required to present our brand as a luxury wine. Our winery is called "Quailbrook Vineyards" and we are focused on extremely high quality hand crafted artisan and estate wines from the Pacific Northwest.
We would like to see designs that utilize a tree line, or other imagery that represents the "Quailbrook" part of our company name. Another interesting feature could be wood grain.
A logo will be required based on your design so please design with this in mind:
This logo should be consistent with the wine bottle label design, and should be representative of our high end exclusive wine while giving a sense of place (Oregon/ Pacific Northwest.)
I will supply an image of the design we received from our local designer, PLEASE NOTE: in general we do like wood grain and tree line concepts but feel the execution was poorly done.
ATTN: Logo design should be suitable for use on: Bottles (Red wine/rose/white wine), Bussiness cards, vehicle signage, business signage, etc
P.S.:
If you have a design that is not outside the box we are still interested in seeing it.
Label is for a burgundy style bottle with a label height of 3.5 - 4" and a width of 3.5-4"
any label <= 4"x4" and >=3.5"x3.5" will be acceptable:
HOWEVER Width should be greater than or equal to height due to the bottle format
Target Market(s)
Wine enthusiasts with adequate discretionary budgets to afford $100 bottles of wine.
Industry/Entity Type
Wine / Winery
Requirements
Must have
- A sense of luxury, a feel of exclusivity, and a theme consistent with our product and brand name
Nice to have
- Tree line, wood grain or other wood themes. Serif fonts
Should not have
- anything cheesy, off topic, hard to read script fonts or anything that makes the label hard to read from a few feet away or too busy

```html
<!DOCTYPE html>
<html lang="en">
<head>
<meta charset="utf-8">
<title>Quailbrook Vineyards — Syrah Label</title>
<link href="https://fonts.googleapis.com/css2?family=Cinzel:wght@500;600;700&display=swap" rel="stylesheet">
<style>
  :root {
    --backdrop: #5a1d1f;
    --label-black: #1c1c1d;
    --silver: #c9ccd0;
    --silver-dark: #8d9096;
    --gold: #d4ac2b;
    --gold-light: #ecd270;
    --gold-deep: #7d5f10;
    --wood-dark: #2a201a;
    --wood-mid: #4a3a2f;
  }
  * { margin: 0; padding: 0; box-sizing: border-box; }
  html, body {
    width: 1200px; height: 900px; overflow: hidden;
    background: var(--backdrop);
    font-family: "Cinzel", "Times New Roman", serif;
  }
  .label {
    position: absolute;
    left: 220px; top: 95px;
    width: 760px; height: 710px;
    background: var(--label-black);
    box-shadow: 0 10px 30px rgba(0,0,0,.35);
  }
  .rules { position: absolute; left: 0; top: 0; }
  .brand-name {
    position: absolute; left: 0; right: 0; top: 70px;
    text-align: center;
    font-size: 78px; font-weight: 700; letter-spacing: 2px;
    color: var(--silver);
    line-height: 1;
  }
  .brand-sub {
    position: absolute; left: 0; right: 0; top: 160px;
    text-align: center;
    font-size: 42px; font-weight: 600; letter-spacing: 2px;
    color: var(--silver);
    line-height: 1;
  }
  .brand-sub .diamond { font-size: 22px; vertical-align: 8px; margin: 0 16px; }
  .treeline {
    position: absolute; left: 20px; right: 20px; top: 222px; height: 210px;
    background:
      radial-gradient(ellipse 60% 55% at 62% 62%, rgba(236,210,112,.95) 0%, rgba(212,172,43,.75) 45%, rgba(125,95,16,0) 100%),
      radial-gradient(ellipse 45% 40% at 22% 78%, rgba(212,172,43,.7) 0%, rgba(125,95,16,0) 100%),
      radial-gradient(ellipse 35% 60% at 92% 40%, rgba(212,172,43,.65) 0%, rgba(125,95,16,0) 100%);
  }
  .region {
    position: absolute; left: 0; right: 0; top: 450px;
    text-align: center;
    font-size: 38px; font-weight: 600; letter-spacing: 1px;
    color: var(--silver);
    line-height: 1;
  }
  .varietal-band {
    position: absolute; left: 0; right: 0; top: 560px; height: 150px;
    background: linear-gradient(180deg, var(--wood-mid) 0%, var(--wood-dark) 30%, var(--wood-mid) 55%, var(--wood-dark) 80%, var(--wood-mid) 100%);
  }
  .varietal {
    position: absolute; left: 0; right: 0; top: 50px;
    text-align: center;
    font-size: 54px; font-weight: 700; letter-spacing: 4px;
    color: var(--gold);
    line-height: 1;
  }
</style>
</head>
<body>
  <main class="label">
    <svg class="rules" width="760" height="710" viewBox="0 0 760 710" aria-hidden="true">
      <g stroke="var(--silver-dark)" stroke-width="2">
        <line x1="14" y1="34" x2="746" y2="34"/>
        <line x1="14" y1="43" x2="746" y2="43"/>
        <line x1="14" y1="512" x2="746" y2="512"/>
        <line x1="14" y1="521" x2="746" y2="521"/>
      </g>
    </svg>
    <h1 class="brand-name">QUAILBROOK</h1>
    <p class="brand-sub"><span class="diamond">◆</span>VINEYARDS<span class="diamond">◆</span></p>
    <div class="treeline" role="img" aria-label="Gold foil evergreen tree line rising from left to right"></div>
    <p class="region">WILLAMETTE VALLEY</p>
    <section class="varietal-band" role="img" aria-label="Dark wood grain band">
      <svg class="rules" width="760" height="150" viewBox="0 0 760 150" aria-hidden="true">
        <g stroke="var(--gold)" stroke-width="2">
          <line x1="14" y1="28" x2="746" y2="28"/>
          <line x1="14" y1="37" x2="746" y2="37"/>
          <line x1="14" y1="117" x2="746" y2="117"/>
          <line x1="14" y1="126" x2="746" y2="126"/>
        </g>
      </svg>
      <p class="varietal">·SYRAH·</p>
    </section>
  </main>
</body>
</html>
```